business card - Helicopter Flight Services, Flight School, etc.

We need a business card design for a new helicopter service.

We offer Helicopter Flight Services, Aerial Filming & Photography, Flight School, and Helicopter Tours. In that order.

Summit BladeAir, Inc.
Dennis Tollerby
SummitBladeair@Kestmail.com
626-418-7352

Based at the Brenwick Airport in Van Nuys, CA. The final design should communicate integrity and safety. Pictures or logos at your discretion.

Card back side - surprise me.

```html
<!DOCTYPE html>
<html lang="en">
<head>
<meta charset="utf-8">
<title>Summit BladeAir, Inc. — Business Card</title>
<link rel="stylesheet" href="https://fonts.googleapis.com/css2?family=Source+Sans+3:wght@400;600&display=swap">
<style>
  :root {
    --bg-top: #2b2b2b;
    --bg-bottom: #060606;
    --card: #ffffff;
    --brand-blue: #2f74c0;
    --ink: #2b2b2b;
    --icon-blue: #3a7cc4;
  }
  * { margin: 0; padding: 0; box-sizing: border-box; }
  html, body {
    width: 1200px; height: 900px; overflow: hidden;
  }
  body {
    background: linear-gradient(180deg, var(--bg-top) 0%, #161616 50%, var(--bg-bottom) 100%);
    font-family: "Source Sans 3", "Myriad Pro", sans-serif;
    position: relative;
  }
  .card {
    position: absolute;
    top: 306px;
    height: 271px;
    background: var(--card);
    border-radius: 10px;
  }
  .card--front { left: 149px; width: 439px; }
  .card--back  { left: 608px; width: 441px; }

  .brand {
    position: absolute;
    left: 26px;
    top: 112px;
    width: 190px;
    display: flex;
    align-items: center;
    gap: 8px;
  }
  .brand__dot {
    flex: none;
    width: 16px; height: 16px;
    border-radius: 50%;
    background: var(--brand-blue);
  }
  .brand__name {
    font-size: 18px;
    font-weight: 600;
    line-height: 1.1;
    color: var(--brand-blue);
  }

  .contact {
    position: absolute;
    left: 239px;
    top: 101px;
  }
  .contact__name {
    font-size: 16px;
    font-weight: 600;
    color: var(--brand-blue);
    margin-bottom: 12px;
  }
  .contact__line {
    display: flex;
    align-items: center;
    gap: 8px;
    font-size: 12.5px;
    line-height: 16px;
    color: var(--ink);
  }
  .contact__line svg { width: 10px; height: 10px; fill: var(--icon-blue); flex: none; }

  .services {
    position: absolute;
    left: 254px;
    top: 102px;
    list-style: none;
  }
  .services li {
    font-size: 12.5px;
    font-weight: 600;
    line-height: 16px;
    color: var(--brand-blue);
  }
</style>
</head>
<body>
  <section class="card card--front" aria-label="Card front">
    <div class="brand">
      <span class="brand__dot"></span>
      <span class="brand__name">Summit BladeAir, Inc.</span>
    </div>
    <div class="contact">
      <p class="contact__name">Dennis Tollerby</p>
      <p class="contact__line">
        <svg viewBox="0 0 10 10" aria-hidden="true"><path d="M2 0.5 L3.6 2.4 L2.8 3.6 C3.4 5 4.8 6.4 6.3 7.1 L7.5 6.3 L9.5 8 L8.3 9.5 C4.5 9.2 0.8 5.5 0.5 1.7 Z"/></svg>
        626-418-7352
      </p>
      <p class="contact__line">
        <svg viewBox="0 0 10 10" aria-hidden="true"><path d="M1 2.5 H9 V8 H1 Z" /><path d="M1 2.5 L5 5.5 L9 2.5" fill="none" stroke="#fff" stroke-width="0.9"/></svg>
        SummitBladeair@Kestmail.com
      </p>
    </div>
  </section>

  <section class="card card--back" aria-label="Card back">
    <div class="brand">
      <span class="brand__dot"></span>
      <span class="brand__name">Summit BladeAir, Inc.</span>
    </div>
    <ul class="services">
      <li>Helicopter Flight Services,</li>
      <li>Aerial Filming &amp; Photography,</li>
      <li>Flight School,</li>
      <li>Helicopter Tours</li>
    </ul>
  </section>
</body>
</html>
```